Health and Fitness Club requires a stunning and simple website

We are a health and fitness club based in Dubai, when we launch we will be the biggest club in the country, we will also have the 2 largest activity rooms in the country, we are setting a new standard in the industry by offering one thing, our attitude.

Our attitude means the following:
unlike other clubs we have no hidden charges or fees
our members can join daily, monthly, 6 months or annually
our service and facility are comparable to 5* hotel gyms
our equipment is second to none
our space is the biggest in the country
we do not force our members to use our in-house personal trainers - you can bring your own and we will not charge them entry!
we will have a cutting edge brawnmesh box in our gym with classes by the best trainers in the country
we will be providing free-lance personal trainers a platform to engage customers, grow their business and even use our activity rooms for classes

Basically we will be a gym like no other, simply because we are gym people and we hate the restrictive practices and hidden charges by other gyms, so we are making our own gym which focuses on quality and service.

All of this has to be communicated in the style of the website, the colors of the website we want to be limited to the logo colors as this will be the same theme running throughout the gym.

The landing page of the website HAS to incorporate elements from our social media presences, this basically is the usual, chirplo, snapvault, kinwall. We can have these as a sidebar, the centre of the page should display the latest article from our blog (also on the website) Also we need to have a calendar for activities and classes on the front page. The menu should have links to the following:
Latest News
About us
Team
Gallery
Membership
Classes
Member Log In
Contact Us
Location

The style of the website has to be similar to the logo, particularly in terms of the fonts used.

```html
<!DOCTYPE html>
<html lang="en">
<head>
<meta charset="utf-8">
<title>Ironhaus Health &amp; Fitness Club</title>
<link href="https://fonts.googleapis.com/css2?family=Anton&family=Source+Sans+3:ital,wght@0,400;0,600;0,700;0,800;1,400&display=swap" rel="stylesheet">
<style>
:root{
  --red:#c0111b;
  --red-dark:#a50d16;
  --ink:#222;
  --text:#3a3a3a;
  --muted:#666;
  --band:#f6f6f6;
  --line:#d8d8d8;
  --icon:#8c8c8c;
  --footer:#3b3e45;
  --footer-low:#2f3237;
  --white:#fff;
}
*{margin:0;padding:0;box-sizing:border-box}
html,body{width:1142px;height:1200px;overflow:hidden;background:var(--white)}
body{position:relative;font-family:"Source Sans 3",sans-serif;color:var(--text)}
.abs{position:absolute}
.topline{left:0;top:0;width:1142px;height:5px;background:var(--red)}
.brand{left:214px;top:22px;display:flex;align-items:center;gap:8px}
.brand-dot{width:34px;height:34px;border-radius:50%;background:var(--ink)}
.brand-name{font-weight:800;font-size:24px;color:var(--red);letter-spacing:.5px}
.utility{right:209px;top:10px;font-size:11px;color:var(--ink);text-transform:uppercase}
.follow{right:209px;top:31px;display:flex;align-items:center;gap:3px;font-size:11px;color:var(--ink)}
.follow span{margin-right:4px}
.sq{display:inline-block;width:20px;height:20px;background:var(--icon)}
.call{right:209px;top:58px;font-size:11px;color:var(--ink);letter-spacing:.3px}
.call b{font-size:16px;font-weight:700;margin-left:3px}
.nav{left:0;top:82px;width:1142px;height:36px;background:var(--red)}
.nav ul{position:absolute;left:201px;top:8px;list-style:none;display:flex;font-weight:700;font-size:15px;color:var(--white);text-transform:uppercase}
.nav li+li::before{content:"|";margin:0 11px}
.search{position:absolute;left:841px;top:6px;width:97px;height:23px;background:var(--white);font-size:9px;font-style:italic;color:#999;padding:5px 9px}
.search svg{position:absolute;right:6px;top:5px}
.hero{left:0;top:118px;width:1142px;height:318px;background:linear-gradient(100deg,#e7e5e2 0%,#dcd8d3 45%,#c9b3a2 70%,#b8927a 85%,#d6d3cf 100%)}
.hero-title{position:absolute;left:200px;top:186px;font-family:"Anton",sans-serif;font-size:44px;line-height:48px;color:#111;text-align:center;width:440px;letter-spacing:.5px}
.dots{position:absolute;left:866px;top:287px;display:flex;gap:4px}
.dots i{width:11px;height:11px;border-radius:50%;background:var(--white);border:1px solid #aaa}
.dots i:first-child{background:var(--red)}
.welcome{left:7px;top:436px;width:1135px;height:112px;background:var(--band);text-align:center}
.welcome h1{margin-top:19px;font-size:17px;font-weight:800;color:var(--red);text-transform:uppercase}
.welcome p{width:620px;margin:4px auto 0;font-size:12.5px;line-height:17px;color:var(--text)}
.social-rail{left:913px;top:444px;width:38px;height:102px;background:#d0d0d0;display:flex;flex-direction:column;align-items:center;gap:4px;padding-top:3px}
.social-rail i{width:30px;height:30px;border-radius:6px}
.shadow{left:140px;top:546px;width:840px;height:16px;background:radial-gradient(ellipse at top,rgba(0,0,0,.14),rgba(0,0,0,0) 70%)}
.h2{font-size:17px;font-weight:800;color:var(--red);text-transform:uppercase}
.photo{background:linear-gradient(135deg,#6a5a4e,#b99377 55%,#3d3a38)}
.article-title{font-size:10.5px;font-weight:600;color:var(--red);line-height:12px;width:185px}
.article-body{font-size:8.6px;line-height:11.5px;color:var(--muted);text-align:justify;width:182px}
.share{display:flex;gap:3px;font-size:6px;color:#555}
.share span{border:1px solid #ccc;padding:1px 3px;border-radius:2px;background:#f4f4f4}
.share .hot{background:#e2553f;color:var(--white);border-color:#e2553f}
.pager-box{left:886px;top:707px;width:54px;height:35px;background:#f2f2f2;display:flex;gap:4px;align-items:center;justify-content:center}
.pager-box i{width:19px;height:18px;background:#ddd;display:flex;align-items:center;justify-content:center}
.why-sub{font-size:13px;font-weight:700;color:var(--red)}
.why-body{font-size:10px;line-height:12.1px;color:var(--ink);text-align:justify;width:301px}
.more{font-size:10px;color:var(--red)}
.cal{left:736px;top:796px;width:172px;height:135px;background:#f1f1f1;border-top:3px solid #9a9a9a;box-shadow:1px 1px 3px rgba(0,0,0,.2)}
.cal table{width:100%;border-collapse:collapse;font-size:8px;font-weight:700;color:#333;text-align:center}
.cal th{background:#8d8d8d;color:var(--white);font-weight:600;height:16px;font-size:9px}
.cal td{height:17px}
.cal td.sun{color:#888}
.cal .year{position:absolute;bottom:5px;width:100%;text-align:center;font-size:11px;color:#aaa;font-weight:700}
.say-line{height:1px;background:var(--line);top:966px}
.avatar{left:539px;top:995px;width:50px;height:50px;border-radius:50%;background:radial-gradient(circle,#c99a80,#7d5b49);border:3px solid var(--white);box-shadow:0 0 3px rgba(0,0,0,.3)}
.quote-mark{font-family:"Anton",sans-serif;font-size:34px;color:#888;line-height:1}
.say-text{left:340px;top:1053px;width:452px;text-align:center;font-size:10px;line-height:12.5px;color:var(--ink)}
.say-name{left:340px;top:1085px;width:452px;text-align:center;font-size:11px;font-style:italic;color:var(--red)}
.bars{left:508px;top:1104px;display:flex;gap:9px;align-items:center}
.bars i{width:15px;height:5px;border:1px solid #999}
.bars i.on{background:var(--red);border-color:var(--red)}
.footer{left:0;top:1130px;width:1142px;height:42px;background:var(--footer)}
.footer ul{position:absolute;left:203px;top:17px;list-style:none;display:flex;font-size:9.5px;color:#bbb;text-transform:uppercase}
.footer li+li::before{content:"|";margin:0 9px}
.footer .fol{position:absolute;left:773px;top:14px;font-size:12px;color:#ccc}
.footer .icons{position:absolute;left:831px;top:9px;display:flex;gap:4px}
.footer .icons i{width:25px;height:25px;background:#777}
.copy{left:0;top:1172px;width:1142px;height:28px;background:var(--footer-low);font-size:8.5px;color:#ddd;padding:9px 0 0 201px}
</style>
</head>
<body>
<div class="abs topline"></div>

<header>
  <div class="abs brand"><span class="brand-dot"></span><span class="brand-name">IRONHAUS</span></div>
  <div class="abs utility">Member Login &nbsp;|&nbsp; Contact Us</div>
  <div class="abs follow"><span>FOLLOW US</span><i class="sq" aria-label="kinwall"></i><i class="sq" aria-label="plusring"></i><i class="sq" aria-label="pinboardly"></i><i class="sq" aria-label="chirplo"></i></div>
  <div class="abs call">CALL US TODAY <b>(555) 010 - 2290</b></div>
</header>

<nav class="abs nav">
  <ul><li>Latest News</li><li>About Us</li><li>Team</li><li>Gallery</li><li>Membership</li><li>Classes</li></ul>
  <div class="search">Search here..
    <svg width="12" height="12" viewBox="0 0 12 12"><circle cx="5" cy="5" r="3.6" fill="none" stroke="#888" stroke-width="1.6"/><line x1="7.6" y1="7.6" x2="11" y2="11" stroke="#888" stroke-width="1.8"/></svg>
  </div>
</nav>

<section class="abs hero" role="img" aria-label="Photo of members training on gym machines">
  <div class="hero-title">HEALTH &amp; FITNESS CLUB<br>IN THE COUNTRY</div>
  <div class="dots"><i></i><i></i><i></i><i></i></div>
</section>

<section class="abs welcome">
  <h1>Welcome to Health &amp; Fitness Club</h1>
  <p>Lorem ipsum dolor sit amet, consectetur adipiscing elit. Nunc sodales, nisi sodales pharetra hendrerit, tellus mi pharetra risus, sed porttitor sapien dui sit Lorem ipsum dolor sit amet, consectetur adipiscing elit. Nunc sodales, nisi sodales</p>
</section>
<aside class="abs social-rail">
  <i style="background:#3b5ea8" aria-label="kinwall"></i>
  <i style="background:#4fb3e6" aria-label="chirplo"></i>
  <i style="background:#6b5647" aria-label="snapvault"></i>
</aside>
<div class="abs shadow"></div>

<h2 class="abs h2" style="left:205px;top:560px">Latest Articles</h2>

<article>
  <div class="abs photo" style="left:203px;top:595px;width:145px;height:124px" role="img" aria-label="Photo of two women chatting at the gym"></div>
  <h3 class="abs article-title" style="left:364px;top:594px">Lorem ipsum dolor sit amet, consectetur adipiscing elit.</h3>
  <p class="abs article-body" style="left:366px;top:625px">Lorem ipsum dolor sit amet, consectetur adipiscing elit. Nunc sodales, nisi sodales pharetra hendrerit, tellus Lorem ipsum dolor sit amet, consectetur adipiscing elit. Nunc sodales, nisi</p>
  <div class="abs share" style="left:364px;top:689px"><span>Like</span><span>3k</span><span>Post</span><span>316</span><span>+1</span><span>81</span><span class="hot">Share</span><span>4k</span></div>
</article>
<article>
  <div class="abs photo" style="left:586px;top:595px;width:145px;height:125px;background:linear-gradient(135deg,#8a5a20,#e3b064 50%,#6e4a22)" role="img" aria-label="Photo of a bright gym floor with members exercising"></div>
  <h3 class="abs article-title" style="left:747px;top:594px">Lorem ipsum dolor sit amet, consectetur adipiscing elit.</h3>
  <p class="abs article-body" style="left:749px;top:625px">Lorem ipsum dolor sit amet, consectetur adipiscing elit. Nunc sodales, nisi sodales pharetra hendrerit, tellus Lorem ipsum dolor sit amet, consectetur adipiscing elit. Nunc sodales, nisi</p>
  <div class="abs share" style="left:747px;top:689px"><span>Like</span><span>3k</span><span>Post</span><span>316</span><span>+1</span><span>81</span><span class="hot">Share</span><span>4k</span></div>
</article>
<div class="abs pager-box">
  <i><svg width="6" height="8"><polyline points="5,1 1,4 5,7" fill="none" stroke="#333" stroke-width="1.3"/></svg></i>
  <i><svg width="6" height="8"><polyline points="1,1 5,4 1,7" fill="none" stroke="#333" stroke-width="1.3"/></svg></i>
</div>

<h2 class="abs h2" style="left:206px;top:752px">Why Choose Us</h2>
<div class="abs photo" style="left:206px;top:783px;width:155px;height:148px;background:linear-gradient(135deg,#b9b1a8,#e8e1d8 50%,#3a5ca8)" role="img" aria-label="Photo of three people stretching on blue mats"></div>
<h3 class="abs why-sub" style="left:377px;top:778px">Lorem ipsum dolor sit amet,</h3>
<p class="abs why-body" style="left:377px;top:800px">Lorem ipsum dolor sit amet, consectetur adipiscing elitLorem ipsum dolor sit amet, consectetur adipiscing elitLorem ipsum dolor sit amet, consectetur adipiscing elitLorem ipsum dolor siLorem ipsum dolor sit amet, consectetur adipiscing elitLorem ipsum dolor sit amet, consectetur adipiscing elitLorem ipsum dolor sit amet, consectetur adipiscing elitLorem ipsum dolor si Lorem ipsum dolor sit amet, consectetur adipiscing elitLorem ipsum dolor sit amet, consectetur adipiscing elitLorem ipsum dolor sit amet, consectetur adipiscing elitLorem ipsum tetur adipiscing elitLorem ipsum dolor si</p>
<a class="abs more" style="left:607px;top:919px">Read More &nbsp;&gt;&gt;</a>

<h2 class="abs h2" style="left:741px;top:753px">Calendar &amp; Events</h2>
<div class="abs" style="left:736px;top:778px;width:172px;text-align:center;font-size:16px;color:var(--red)">FEBRUARY</div>
<div class="abs cal">
  <table>
    <tr><th>S</th><th>M</th><th>T</th><th>W</th><th>T</th><th>F</th><th>S</th></tr>
    <tr><td></td><td></td><td></td><td></td><td></td><td></td><td>1</td></tr>
    <tr><td class="sun">2</td><td>3</td><td>4</td><td>5</td><td>6</td><td>7</td><td>8</td></tr>
    <tr><td class="sun">9</td><td>10</td><td>11</td><td>12</td><td>13</td><td>14</td><td>15</td></tr>
    <tr><td class="sun">16</td><td>17</td><td>18</td><td>19</td><td>20</td><td>21</td><td>22</td></tr>
    <tr><td class="sun">23</td><td>24</td><td>25</td><td>26</td><td>27</td><td>28</td><td></td></tr>
  </table>
  <div class="year">2014</div>
</div>

<div class="abs say-line" style="left:413px;width:70px"></div>
<div class="abs" style="left:456px;top:954px;width:1px;height:24px;background:var(--line)"></div>
<h2 class="abs h2" style="left:477px;top:957px">Our Customer Say</h2>
<div class="abs" style="left:656px;top:954px;width:1px;height:24px;background:var(--line)"></div>
<div class="abs say-line" style="left:630px;width:70px"></div>

<div class="abs avatar" role="img" aria-label="Portrait of the reviewing member"></div>
<div class="abs quote-mark" style="left:270px;top:1048px">“</div>
<div class="abs quote-mark" style="left:838px;top:1048px">”</div>
<p class="abs say-text">Lorem ipsum dolor sit amet, consectetur adipiscing elitLorem ipsum dolor sit amet, consectetur adipiscing elitLorem ipsum dolor sit amet, consectetur adipiscing elitLorem ipsum d</p>
<div class="abs say-name">-- Dara Wellin</div>
<div class="abs bars">
  <svg width="9" height="12"><polyline points="8,1 2,6 8,11" fill="none" stroke="#555" stroke-width="2"/></svg>
  <i></i><i class="on"></i><i></i>
  <svg width="9" height="12"><polyline points="1,1 7,6 1,11" fill="none" stroke="#555" stroke-width="2"/></svg>
</div>

<footer class="abs footer">
  <ul><li>Latest News</li><li>About Us</li><li>Team</li><li>Gallery</li><li>Membership</li><li>Classes</li></ul>
  <span class="fol">Follow us</span>
  <div class="icons"><i aria-label="kinwall"></i><i aria-label="plusring"></i><i aria-label="pinboardly"></i><i aria-label="chirplo"></i></div>
</footer>
<div class="abs copy">© 2014, All Rights Reserved</div>
</body>
</html>
```